PowerPoint Re-Design and Template Needs a Designer's Eye!

I have the text, images and logo for a PowerPoint but need your Design and Template skills! Less than 20 pages, needs to be concise, include images, must have creative page layouts, include our floater-logo on every page, use sidebars or call-outs for important information, have color but not too much because this will be printed many times (our current colors are too dark). You can use bullet-points or paragraphs. You can also change the titles, font, color, layout - anything! This is YOUR PowerPoint to create the most impressive Template! We are an investment management firm located in New York City. Our investment returns are the very best in the industry and we want this PowerPoint to convey our "best in class" style.

Notes:
1) Please use the PPP outline attached.
2) I have attached a rough draft PPP. Please use the logos on page 2. Some pages do not have text, the final text will be available shortly.
3) I have attached examples you can reference.
4) Please include our floater-logo on every page.
5) Please feel free to ask questions or clarification.

Hi Designers, Thank you very much for your wonderful submissions! My partners and I are going through each submission in detail today and tomorrow. We'll be in touch over the next few days with additional questions and comments. Stay tuned! Best, Damon Quillfeather

High-net worth individuals and institutions. New York City, Wall Street.

Investment

• - Floater-logo on every page
- Sidebars or call-outs on several pages (you can decide which ones)
- Please include images; however, the PPP Template is the most important.

```html
<!DOCTYPE html>
<html lang="en">
<head>
<meta charset="utf-8">
<title>Strategy: Investment Universe</title>
<link href="https://fonts.googleapis.com/css2?family=Roboto+Condensed:wght@400;700&family=Questrial&display=swap" rel="stylesheet">
<style>
  :root {
    --brand-orange: #f47b00;
    --ink: #111111;
    --body-text: #4a4a4a;
    --rule-grey: #c9c9c9;
    --footer-grey: #5b5b5b;
    --white: #ffffff;
  }
  * { margin: 0; padding: 0; box-sizing: border-box; }
  html, body { width: 1200px; height: 900px; overflow: hidden; background: var(--white); }
  .slide {
    position: relative;
    width: 1200px;
    height: 900px;
    background: var(--white);
    font-family: "Questrial", "Century Gothic", sans-serif;
    overflow: hidden;
  }
  .slide-header {
    position: absolute;
    left: 0; top: 0;
    width: 100%;
    height: 98px;
    background: var(--brand-orange);
    border-bottom: 3px solid var(--rule-grey);
  }
  .slide-title {
    position: absolute;
    left: 27px;
    top: 26px;
    font-family: "Roboto Condensed", "Arial Narrow", sans-serif;
    font-weight: 700;
    font-size: 40px;
    line-height: 1;
    color: var(--ink);
    letter-spacing: 0.2px;
  }
  .firm-mark {
    position: absolute;
    right: 22px;
    top: 22px;
    display: flex;
    align-items: center;
    gap: 12px;
  }
  .firm-mark__dot {
    width: 52px; height: 52px;
    border-radius: 50%;
    background: var(--white);
  }
  .firm-mark__name {
    font-family: "Roboto Condensed", "Arial Narrow", sans-serif;
    font-weight: 700;
    font-size: 24px;
    color: var(--white);
  }
  .strategy-copy {
    position: absolute;
    left: 80px;
    top: 140px;
    width: 1045px;
    color: var(--body-text);
    font-size: 21.5px;
    line-height: 39px;
  }
  .strategy-copy p + p { margin-top: 39px; }
  .key-points {
    position: absolute;
    left: 77px;
    top: 468px;
    list-style: none;
  }
  .key-points li {
    display: flex;
    align-items: center;
    height: 42px;
    margin-bottom: 26px;
    color: var(--brand-orange);
    font-size: 25px;
  }
  .key-points__icon {
    width: 38px; height: 38px;
    margin-right: 20px;
    flex: none;
  }
  .slide-footer {
    position: absolute;
    left: 0; bottom: 0;
    width: 100%;
    height: 40px;
    background: var(--footer-grey);
    color: var(--white);
    font-family: "Roboto Condensed", "Arial Narrow", sans-serif;
    font-size: 19px;
    display: flex;
    justify-content: space-between;
    align-items: center;
    padding: 0 12px 0 9px;
  }
</style>
</head>
<body>
<main class="slide">
  <header class="slide-header">
    <h1 class="slide-title">STRATEGY: INVESTMENT UNIVERSE</h1>
    <div class="firm-mark">
      <span class="firm-mark__name">Corvane Capital</span>
      <span class="firm-mark__dot"></span>
    </div>
  </header>

  <section class="strategy-copy">
    <p>To purchase domestic and foreign securities that offer superior risk-adjusted returns. We are thematic at the macro-level and use a bottom-up, research-intensive evaluation process at the sector and security level.</p>
    <p>Of significant importance to us is evaluating opportunities at both the quantitative and qualitative levels. Once a security has been selected for investment, a risk-budget is assigned to it based on possible outcomes and the potential risk/reward ratio.</p>
  </section>

  <ul class="key-points">
    <li><svg class="key-points__icon" viewBox="0 0 38 38" aria-hidden="true"><circle cx="19" cy="19" r="18" fill="var(--brand-orange)"/></svg>Long-biased small, mid and large cap domestic and foreign securities.</li>
    <li><svg class="key-points__icon" viewBox="0 0 38 38" aria-hidden="true"><circle cx="19" cy="19" r="18" fill="var(--brand-orange)"/></svg>Hold 20-35 positions from several months to many years.</li>
    <li><svg class="key-points__icon" viewBox="0 0 38 38" aria-hidden="true"><circle cx="19" cy="19" r="18" fill="var(--brand-orange)"/></svg>All dividends are used to purchase additional securities.</li>
  </ul>

  <footer class="slide-footer">
    <span class="slide-footer__author">Damon Quillfeather 2015</span>
    <span class="slide-footer__page">Page : 01</span>
  </footer>
</main>
</body>
</html>
```